Brightmill Data Works

Our company is about IT hardwares and IT solutions. IT hardware such as PC, RAMS, storage and servers. IT solutions such as project management, BA. We are also selling new technology too.

Target Market(s)

Consumer, Small to Medium Business, Corporate

Requirements
Must have
• The business card must have the following:
• Name:
• Title:
• Contact Number:
• Email address:
• Website:
• Color: Must match the logo color upgrade

```html
<!DOCTYPE html>
<html lang="en">
<head>
<meta charset="UTF-8">
<title>Brightmill Data Works – Business Card</title>
<link href="https://fonts.googleapis.com/css2?family=Open+Sans:wght@400;600;700&display=swap" rel="stylesheet">
<style>
  :root {
    --backdrop: #1c1c1d;
    --card: #111112;
    --accent: #e08a2a;
    --accent-deep: #c96f18;
    --ink: #f2f2f2;
    --ink-soft: #d6d6d6;
    --rule: #bdbdbd;
  }
  * { margin: 0; padding: 0; box-sizing: border-box; }
  html, body {
    width: 1200px; height: 900px; overflow: hidden;
    background: var(--backdrop);
    font-family: "Open Sans", Arial, sans-serif;
  }
  .stage {
    width: 1200px; height: 900px;
    display: flex; flex-direction: column;
    align-items: center; justify-content: center; gap: 60px;
  }
  .card {
    position: relative;
    width: 525px; height: 300px;
    background: var(--card);
    border-radius: 18px;
    box-shadow: 0 10px 30px rgba(0,0,0,.5);
    color: var(--ink);
  }
  /* front */
  .card-front { display: flex; flex-direction: column; align-items: center; justify-content: center; }
  .front-brand { display: flex; align-items: center; gap: 12px; margin-top: -20px; }
  .brand-square { width: 22px; height: 22px; background: var(--accent); }
  .front-brand-name { font-size: 30px; font-weight: 700; color: var(--accent); letter-spacing: .5px; }
  .tagline {
    position: absolute; bottom: 62px; left: 0; right: 0;
    text-align: center; font-size: 13px; font-weight: 600; letter-spacing: .3px;
    color: var(--ink-soft);
  }
  /* back */
  .back-brand {
    position: absolute; top: 52px; right: 34px;
    font-size: 24px; font-weight: 700; color: var(--ink); text-align: right; line-height: 1.1;
  }
  .back-rule {
    position: absolute; top: 128px; left: 205px; right: 34px;
    height: 1px; background: var(--rule); transform: rotate(0deg);
  }
  .contact-list {
    position: absolute; top: 140px; right: 34px;
    list-style: none; text-align: right;
    font-size: 13.5px; line-height: 20px; color: var(--ink);
  }
  .contact-list li { display: flex; align-items: center; justify-content: flex-end; gap: 6px; }
  .contact-list svg { width: 10px; height: 10px; fill: var(--accent); }
  .person {
    position: absolute; left: 30px; top: 210px;
  }
  .person-name { font-size: 18px; font-weight: 600; color: var(--accent); letter-spacing: .5px; }
  .person-title { font-size: 15px; color: var(--ink); margin-top: -2px; }
</style>
</head>
<body>
<main class="stage">
  <section class="card card-front">
    <div class="front-brand">
      <span class="brand-square"></span>
      <span class="front-brand-name">Brightmill Data Works</span>
    </div>
    <p class="tagline">IT HARDWARES AND IT SOLUTIONS</p>
  </section>

  <section class="card card-back">
    <div class="back-brand">Brightmill Data Works</div>
    <div class="back-rule"></div>
    <ul class="contact-list">
      <li>044-555 210 384
        <svg viewBox="0 0 10 10" aria-hidden="true"><path d="M2 1h2l1 2-1 1a5 5 0 0 0 2 2l1-1 2 1v2c0 1-1 1-1 1A7 7 0 0 1 1 2s0-1 1-1z"/></svg></li>
      <li>hello@brightmill.net
        <svg viewBox="0 0 10 10" aria-hidden="true"><path d="M0 2h10v6H0z M0 2l5 3.5L10 2" stroke="#111112" stroke-width=".8"/></svg></li>
      <li>www.brightmill.net
        <svg viewBox="0 0 10 10" aria-hidden="true"><circle cx="5" cy="5" r="5"/><path d="M0 5h10M5 0c-2 3-2 7 0 10M5 0c2 3 2 7 0 10" stroke="#111112" stroke-width=".7" fill="none"/></svg></li>
    </ul>
    <div class="person">
      <p class="person-name">DANIEL HARTLEY</p>
      <p class="person-title">Managing Director</p>
    </div>
  </section>
</main>
</body>
</html>
```